Brochure design for International Beauty Trade Show

I neee a tri-fold company products' brochure to distribute to customers at an international trade show coming soon. We have 4 main product categories- hair and skincare, facial care, Body and bath and massage oil.
The brochure needs to include at least 2 photos of the main products of each category, benefits, call to action and our company contact info ( website and phone number).

Target Market(s)

Educated and high income earners looking for all-natural,pure, 100 organic products for their beauty and personal care needs. Our products cross all racial groups/demographics and suitable for all skin types

Industry/Entity Type

Hair And Beauty

Font styles to use
Serif

Colors

Designer to choose colors to be used in the design.

Requirements
Must have
• The design must stand out as pure and luxury and at the same time be inclusive using our logo design colors- orange and blue. Also, the content must be easy to read and captivating.
• Finally if using women pictures, please include Black, white, Asian and Latina to reflect the fact that our products are suitable for all skin types.
Nice to have
• Design the brochure such that it could be printed as a poster-banner ad.
Should not have
• Cookie cutter designs are not welcome

```html
<!DOCTYPE html>
<html lang="en">
<head>
<meta charset="utf-8">
<title>Lumera Naturals – Trade Show Brochure</title>
<link rel="stylesheet" href="https://fonts.googleapis.com/css2?family=Didact+Gothic&family=Montserrat:wght@600;700&display=swap">
<style>
  :root {
    --orange: #e8690f;
    --blue: #1f86c8;
    --ink: #222222;
    --paper: #ffffff;
    --backdrop: #e9e6e1;
  }
  * { box-sizing: border-box; margin: 0; padding: 0; }
  html, body { width: 830px; height: 1200px; overflow: hidden; }
  body {
    background: var(--backdrop);
    position: relative;
    font-family: "Didact Gothic", "Century Gothic", sans-serif;
    color: var(--ink);
  }
  .brochure-side {
    position: absolute;
    left: 102px;
    width: 634px;
    height: 490px;
    background: var(--paper);
    overflow: hidden;
    box-shadow: 0 3px 10px rgba(0,0,0,.18);
  }
  .side-outer { top: 80px; }
  .side-inner { top: 622px; }
  .swoosh { position: absolute; left: 0; top: 0; width: 634px; height: 490px; }
  .placeholder { position: absolute; border-radius: 6px; }
  .about {
    position: absolute; left: 217px; top: 0; width: 196px; height: 178px;
    background: rgba(70,140,50,.55);
    color: #fff; text-align: center; padding: 16px 18px 0;
  }
  .about h2 { font-family: "Montserrat", sans-serif; font-weight: 600; font-size: 17px; letter-spacing: .5px; margin-bottom: 10px; }
  .about p { font-size: 10.5px; line-height: 16px; }
  .headline {
    position: absolute; left: 420px; top: 40px; width: 204px; text-align: right; color: #fff;
    text-shadow: 0 1px 3px rgba(0,0,0,.35);
  }
  .headline strong { display: block; font-family: "Montserrat", sans-serif; font-weight: 700; font-size: 21px; line-height: 24px; }
  .headline span { display: block; font-size: 19px; line-height: 22px; }
  .category { position: absolute; }
  .category h3 { font-family: "Didact Gothic", sans-serif; font-weight: 400; font-size: 25px; line-height: 27px; color: var(--orange); }
  .category.blue h3 { color: var(--blue); }
  .benefits { list-style: none; margin-top: 12px; }
  .benefits li { position: relative; font-size: 9.4px; line-height: 16px; padding-left: 16px; white-space: nowrap; }
  .benefits li::before {
    content: ""; position: absolute; left: 0; top: 4px; width: 8px; height: 8px;
    border: 1px solid var(--orange);
  }
  .benefits li::after {
    content: ""; position: absolute; left: 3px; top: 3px; width: 3px; height: 6px;
    border: solid var(--orange); border-width: 0 1.5px 1.5px 0; transform: rotate(40deg);
  }
  .blue .benefits li::before, .blue .benefits li::after { border-color: var(--blue); }
  .hair { left: 22px; top: 288px; }
  .hair .benefits { margin-top: 18px; }
  .mark-circle { position: absolute; left: 274px; top: 322px; width: 68px; height: 68px; border-radius: 50%; background: var(--orange); }
  .contact { position: absolute; left: 224px; top: 408px; width: 170px; text-align: center; font-family: "Montserrat", sans-serif; font-weight: 700; font-size: 10.2px; line-height: 17.5px; }
  .brand { position: absolute; left: 448px; top: 385px; display: flex; align-items: center; gap: 8px; }
  .brand .dot { width: 24px; height: 24px; border-radius: 50%; background: var(--orange); }
  .brand .name { font-size: 25px; color: var(--orange); letter-spacing: 2px; }
  .brand-web { position: absolute; left: 440px; top: 446px; width: 170px; text-align: center; font-size: 10px; color: var(--blue); }
  .facial { left: 19px; top: 222px; }
  .bath { left: 232px; top: 324px; }
  .massage { left: 441px; top: 152px; }
  .massage .benefits { margin-top: 14px; }
</style>
</head>
<body>

<section class="brochure-side side-outer">
  <svg class="swoosh" viewBox="0 0 634 490" role="img" aria-label="Spa photograph: bamboo leaves, black massage stones and a purple orchid">
    <defs>
      <linearGradient id="spaGreenTop" x1="0" y1="0" x2="1" y2="0.3">
        <stop offset="0" stop-color="#eef5e6"/>
        <stop offset="0.35" stop-color="#8fc05a"/>
        <stop offset="0.7" stop-color="#4f9a35"/>
        <stop offset="1" stop-color="#2f7d2a"/>
      </linearGradient>
    </defs>
    <path d="M0 0H634V290C500 300 380 270 270 220C180 180 80 165 0 185Z" fill="url(#spaGreenTop)"/>
    <path d="M0 185C80 165 180 180 270 220C380 270 500 300 634 290V312C520 318 400 290 300 245C200 200 100 185 0 195Z" fill="var(--orange)"/>
    <path d="M220 205C330 265 480 312 634 310V318C470 320 320 275 220 205Z" fill="var(--blue)"/>
  </svg>
  <div class="placeholder" role="img" aria-label="Three amber hair and argan oil bottles with pump tops" style="left:30px;top:68px;width:130px;height:196px;background:linear-gradient(180deg,#f4efe6,#d9a36a);opacity:.9"></div>
  <div class="placeholder" role="img" aria-label="Photo of a woman with long dark hair beside spa stones and an orchid" style="left:430px;top:110px;width:204px;height:150px;background:linear-gradient(160deg,#3d7a2d,#5a4437 60%,#c99a86);opacity:.55"></div>

  <div class="about">
    <h2>ABOUT US:</h2>
    <p>Lumera Naturals is an export/import company. Our mission is to satisfy our customers by supplying them with pure, 100% organic products, that make them more attractive and solve the most common skin and hair problems</p>
  </div>
  <div class="headline">
    <strong>Natural Solutions</strong>
    <span>to Forever Beauty</span>
  </div>

  <div class="category hair">
    <h3>Hair &amp;<br>Skincare</h3>
    <ul class="benefits">
      <li>Natural moisturizer</li>
      <li>Heal damaged hair or sensitive scalp</li>
      <li>Soften curly and frizzy hair</li>
      <li>Antiaging, remove wrinkles</li>
      <li>Reduce sebum secretion</li>
      <li>Tone, sooth and restore luster</li>
      <li>Restore fair complexion</li>
    </ul>
  </div>

  <div class="mark-circle"></div>
  <div class="contact">
    (800) 555-0147<br>
    hello@lumeranaturals.com<br>
    www.lumeranaturals.com
  </div>

  <div class="brand"><span class="dot"></span><span class="name">LUMERA</span></div>
  <div class="brand-web">www.lumeranaturals.com</div>
</section>

<section class="brochure-side side-inner">
  <svg class="swoosh" viewBox="0 0 634 490" role="img" aria-label="Spa photograph: woman applying cream, green bamboo, black stones, purple orchid and a lit candle">
    <defs>
      <linearGradient id="spaGreenInner" x1="0" y1="0" x2="1" y2="0.4">
        <stop offset="0" stop-color="#a67c62"/>
        <stop offset="0.25" stop-color="#5d8f3a"/>
        <stop offset="0.6" stop-color="#2f4a2a"/>
        <stop offset="1" stop-color="#7fae45"/>
      </linearGradient>
    </defs>
    <path d="M0 0H634V112C590 112 530 120 450 150C350 190 200 200 0 165Z" fill="url(#spaGreenInner)"/>
    <path d="M0 165C200 200 350 190 450 150C530 120 590 112 634 112V146C560 128 490 126 420 146C310 186 150 196 0 180Z" fill="var(--orange)"/>
    <path d="M0 186C150 204 300 198 415 162C300 206 150 214 0 200Z" fill="var(--blue)"/>
  </svg>

  <div class="category facial">
    <h3>Facial Care</h3>
    <ul class="benefits">
      <li>Reduce sebum secretion</li>
      <li>Eliminate toxins &amp; blemishes</li>
      <li>Tighten pores</li>
      <li>Dries pimples</li>
      <li>Remove blackheads</li>
    </ul>
  </div>
  <div class="placeholder" role="img" aria-label="Jar of facial clay mask and boxed green clay powder" style="left:18px;top:350px;width:168px;height:120px;background:linear-gradient(135deg,#f3f1ec,#a9d4a0)"></div>

  <div class="placeholder" role="img" aria-label="Boxed natural soaps with lemon and prickly pear fruit" style="left:230px;top:200px;width:180px;height:118px;background:linear-gradient(135deg,#7fbf5a,#f2d24a 45%,#d9474f)"></div>
  <div class="category bath blue">
    <h3>Body &amp;<br>Bath Care</h3>
    <ul class="benefits">
      <li>Purify and disinfect</li>
      <li>Fight &nbsp;acne</li>
      <li>Rejuvenate &amp; hydrate</li>
      <li>Promote healthy looking skin</li>
      <li>Remove dead cells</li>
    </ul>
  </div>

  <div class="category massage">
    <h3>Massage<br>Care</h3>
    <ul class="benefits">
      <li>Relief stress and pain</li>
      <li>Fight muscle contraction/tenderness</li>
      <li>Eliminate stretch marks</li>
      <li>Pure, undiluted</li>
    </ul>
  </div>
  <div class="placeholder" role="img" aria-label="Dark massage oil spray bottle with red berries" style="left:470px;top:292px;width:160px;height:188px;background:linear-gradient(180deg,#f5f5f5,#3a3566 45%,#c8323a)"></div>
</section>

</body>
</html>
```